Website Design for a Project Management Consulting Business

I have a logo design already and now I need a website.
I am a project manager and run my own consulting business.
Currently I am under contract with 3 major Vantage 400 companies. I'd like a website I can direct current and future clients.
My job is running IT projects and working with developers to deliver business priorities.
The website should be professional and clean - I work IT projects and would like to incorporate that into any theme.
I'd like the site to have several page or breakoff links - sections would include : about me, about my services, a page to display all of my certification badges, another page to talk about highlights from past projects and so on.
Looking for a collaborative experience.

Industry/Entity Type

Vantage 400 Consulting Firm - Project Management

Coding

Coded - Design and coding required

Number of Pages Required

1 page

Font styles to use
Serif

Colors
0094D4
00A9DD
6FCCEA
C7EBF8
E9F6FB
EE7325
F08F49
F5BC92
FAE3D3
FDF4ED

Requirements
Must have
• Sections that are a must: About Me (bio), About My Services, About my Certifications and Credentials, Experience on Past Projects,
Nice to have
• I have added the logo below - I'd like to use the logo and have it prominent ; should be professional and inviting

```html
<!DOCTYPE html>
<html lang="en">
<head>
<meta charset="utf-8">
<title>Keystone Project Consulting</title>
<link href="https://fonts.googleapis.com/css2?family=Roboto:wght@300;400;500;700;900&family=Archivo+Black&display=swap" rel="stylesheet">
<style>
:root{
  --navy:#0b3c73;
  --blue:#0a6fb8;
  --bright:#0094d4;
  --sky:#00a9dd;
  --ink:#222;
  --muted:#777;
  --soft:#f2f2f2;
  --footer:#2f2f2f;
  --white:#fff;
}
*{margin:0;padding:0;box-sizing:border-box}
html,body{width:1200px;height:3169px;overflow:hidden}
body{font-family:'Roboto',sans-serif;color:var(--ink);background:var(--white);position:relative}
.abs{position:absolute}

/* header */
.site-header{top:0;left:0;width:1200px;height:102px;border-top:5px solid var(--blue);background:var(--white)}
.brand{left:42px;top:30px;display:flex;align-items:center;gap:10px}
.brand-mark{width:38px;height:38px;border:3px solid var(--navy)}
.brand-name{font-weight:700;font-size:20px;color:var(--navy);letter-spacing:.5px;line-height:1.1}
.main-nav{left:353px;top:47px;display:flex;gap:27px}
.main-nav a{font-size:13.5px;font-weight:500;color:#222;text-decoration:none}
.main-nav a.active{color:var(--bright)}
.social{display:flex;gap:5px}
.social span{display:flex;align-items:center;justify-content:center;width:37px;height:37px;border-radius:50%;background:#fff;box-shadow:0 2px 6px rgba(0,0,0,.18);font-size:11px;font-weight:700;color:var(--navy);letter-spacing:.3px}
.social span.primary{background:var(--navy);color:#fff}
.header-social{left:1038px;top:35px}

/* hero */
.hero{top:102px;left:0;width:1200px;height:601px}
.hero-panel{left:0;top:0;width:600px;height:601px;background:linear-gradient(135deg,#1a8fd6 0%,#0b64ad 55%,#0a3f7a 100%)}
.hero-photo{left:600px;top:0;width:600px;height:601px;background:linear-gradient(120deg,#d9dde2 0%,#9aa6b3 40%,#3d4a5c 70%,#cfd5dc 100%)}
.hero-title{left:108px;top:128px;font-family:'Archivo Black',sans-serif;font-size:46px;line-height:64px;color:#fff;letter-spacing:.5px}
.hero-text{left:111px;top:328px;width:420px;font-size:17px;font-weight:500;line-height:26px;color:#fff}
.btn-outline{display:block;position:absolute;font-size:13.5px;font-weight:700;text-align:center;text-transform:uppercase;text-decoration:none}
.btn-outline::after{content:"";position:absolute;left:6px;top:6px;right:-6px;bottom:-6px;border:2px solid currentColor;pointer-events:none}
.hero-btn{left:112px;top:405px;width:146px;height:50px;line-height:50px;background:#fff;color:#111}
.hero-btn::after{border-color:#fff}
.dots{left:111px;top:566px;display:flex;gap:5px;align-items:center}
.dots i{display:block;width:12px;height:12px;border:1.5px solid #fff;border-radius:50%}
.dots i.on{background:#fff}
.dots b{display:block;width:94px;height:2px;background:#fff;margin-left:12px}

/* headings */
.section-title{font-size:36px;font-weight:700;color:var(--navy);display:flex;align-items:center;gap:16px;letter-spacing:.5px}
.section-title .rule{display:block;width:44px;height:2px;background:var(--bright)}
.section-title .light{color:#888}
.section-title.center{left:0;width:1200px;justify-content:center}

/* about */
.about-accent{left:130px;top:783px;width:129px;height:129px;background:linear-gradient(180deg,#0a7fcb,#0a3f7a)}
.about-frame{left:155px;top:808px;width:316px;height:434px;background:#fff;box-shadow:0 4px 14px rgba(0,0,0,.18);padding:8px}
.about-photo{width:100%;height:100%;background:linear-gradient(180deg,#e4e6e9 0%,#8596ae 45%,#4b5f7d 100%)}
.dot-grid{left:385px;top:1150px}
.about-title{left:576px;top:820px}
.about-copy{left:576px;top:889px;width:494px;font-size:15px;font-weight:300;line-height:25.7px;color:#555;text-align:justify}
.about-copy p+p{margin-top:12px}
.about-copy strong{color:var(--bright);font-weight:500}
.btn-solid{left:576px;top:1162px;width:136px;height:50px;line-height:50px;background:linear-gradient(180deg,#0b74c0,#0a4a8a);color:#fff}
.btn-solid::after{border-color:var(--navy)}

/* services */
.services{left:0;top:1351px;width:1200px;height:612px;background:var(--soft)}
.services-title{top:60px}
.service-card{top:138px;width:309px;height:408px;background:#fff;box-shadow:0 2px 8px rgba(0,0,0,.06);text-align:center}
.service-card.featured{background:linear-gradient(180deg,#0a74bf,#0a3a70)}
.service-img{margin:2px;height:200px;background:linear-gradient(135deg,#dfe3e8,#9aa4b1 55%,#c9ced5)}
.service-card.featured .service-img{margin:5px 7px;height:192px}
.service-card h3{margin-top:24px;font-size:19px;font-weight:500;color:#333}
.service-card p{margin:14px auto 0;width:270px;font-size:14px;font-weight:300;line-height:25px;color:#777}
.service-card.featured h3,.service-card.featured p{color:#fff;font-weight:400}
.card-btn{left:94px;top:350px;width:116px;height:42px;line-height:42px;font-size:11.5px;background:linear-gradient(180deg,#0b74c0,#0a4a8a);color:#fff}
.card-btn::after{border-color:var(--navy)}
.featured .card-btn{background:#fff;color:#222}
.featured .card-btn::after{border-color:#fff}

/* certifications */
.certs{left:0;top:1963px;width:1200px;height:367px;background:radial-gradient(ellipse at 50% 0%,#1a9be0 0%,#0a68b2 50%,#073f7a 100%)}
.certs-title{top:38px;color:#fff}
.certs-title .rule{background:#fff}
.badge-ring{top:123px;width:192px;height:192px;border-radius:50%;border:7px solid rgba(255,255,255,.55);display:flex;align-items:center;justify-content:center}
.badge-core{width:136px;height:136px;border-radius:50%;background:#fff;display:flex;align-items:center;justify-content:center}
.badge-shape{width:86px;height:86px;border-radius:50%;background:radial-gradient(circle,#f5bc92 0%,#f08f49 55%,#ee7325 100%)}

/* projects */
.projects-title{top:2392px}
.project{width:232px}
.project-img{background:linear-gradient(135deg,#e2e5e9,#98a3b1 55%,#5b6a7e)}
.project h4{position:absolute;left:0;top:268px;width:232px;text-align:center;font-size:19px;font-weight:500;color:#333}

/* footer */
.site-footer{left:0;top:2858px;width:1200px;height:311px;background:var(--footer);color:#fff}
.footer-brand{left:111px;top:100px;display:flex;align-items:center;gap:10px}
.footer-brand .brand-mark{border-color:#fff}
.footer-brand .brand-name{color:#fff;font-size:19px}
.footer-social{left:184px;top:174px}
.footer-social span{width:30px;height:30px;background:#444;box-shadow:none;color:#fff;font-size:9.5px}
.footer-social span.primary{background:#fff;color:var(--navy)}
.footer-col h5{font-size:16px;font-weight:700;letter-spacing:.2px}
.footer-col h5::after{content:"";display:block;width:40px;height:2px;background:var(--bright);margin-top:6px}
.footer-col ul{list-style:none;margin-top:14px}
.footer-col li{display:flex;align-items:flex-start;gap:17px;font-size:15px;line-height:22px;margin-bottom:11px;color:#eee}
.footer-col li svg{flex:none;margin-top:5px}
.footer-rule{left:111px;top:266px;width:978px;height:1px;background:#555}
.copyright{left:0;top:280px;width:1200px;text-align:center;font-size:12px;color:#ddd}
.copyright b{font-weight:700}
</style>
</head>
<body>

<header class="site-header abs">
  <div class="brand abs"><span class="brand-mark"></span><span class="brand-name">KEYSTONE<br>PROJECT CONSULTING</span></div>
  <nav class="main-nav abs">
    <a class="active" href="#">HOME</a><a href="#">ABOUT ME</a><a href="#">SERVICES</a><a href="#">CERTIFICATIONS</a><a href="#">PROJECTS</a><a href="#">BLOG</a><a href="#">CONTACT US</a>
  </nav>
  <div class="social header-social abs" aria-label="Social profiles"><span class="primary">FB</span><span>TW</span><span>LI</span></div>
</header>

<section class="hero abs">
  <div class="hero-panel abs"></div>
  <div class="hero-photo abs" role="img" aria-label="Two consultants reviewing a tablet at an office table"></div>
  <h1 class="hero-title abs">KEYSTONE<br>PROJECT<br>CONSULTING</h1>
  <p class="hero-text abs">Lorem ipsum dolor sit amet, consectetur adipiscing elit, sed do eiusmod temporea.</p>
  <a class="btn-outline hero-btn" href="#">Get Started</a>
  <div class="dots abs"><i></i><i class="on"></i><i></i><i></i><i></i><b></b></div>
</section>

<section class="about">
  <div class="about-accent abs"></div>
  <svg class="dot-grid abs" width="130" height="130" aria-hidden="true">
    <defs><pattern id="dots" width="8" height="8" patternUnits="userSpaceOnUse"><circle cx="2" cy="2" r="1" fill="#c8c8c8"/></pattern></defs>
    <rect x="86" y="0" width="44" height="130" fill="url(#dots)"/>
    <rect x="0" y="92" width="130" height="38" fill="url(#dots)"/>
  </svg>
  <div class="about-frame abs"><div class="about-photo" role="img" aria-label="Portrait of the consultant in a blue plaid suit"></div></div>
  <h2 class="section-title about-title abs"><span class="rule"></span><span>ABOUT <span class="light">ME</span></span></h2>
  <div class="about-copy abs">
    <p><strong>DANIEL WHITMORE</strong> is the Owner of Keystone Project Consulting, LLC and serves as Principal Lead Consultant on waterfall and agile contract opportunities. Keystone Project Consulting, LLC has engaged on a contract basis with Vantage 400 companies across various industries including banking and credit unions, global supply chain, and international food distribution.</p>
    <p>Dan Whitmore brings 12 years of experience to his clients encompassing various project methodologies including: waterfall, agile, and hybrid frameworks.</p>
  </div>
  <a class="btn-outline btn-solid" href="#">Learn More</a>
</section>

<section class="services abs">
  <h2 class="section-title center services-title abs"><span class="rule"></span><span><span class="light">MY</span> SERVICES</span><span class="rule"></span></h2>
  <article class="service-card abs" style="left:111px">
    <div class="service-img" role="img" aria-label="Two colleagues working at a laptop"></div>
    <h3>LOREM IPSUM DOL</h3>
    <p>Lorem ipsum dolor sit amet, consectetur adipi scing elit, sed do eiusmod tempor incididunt ut laborea.</p>
    <a class="btn-outline card-btn" href="#">Learn More</a>
  </article>
  <article class="service-card featured abs" style="left:446px">
    <div class="service-img" role="img" aria-label="Team meeting around a laptop in an office"></div>
    <h3>LOREM IPSUM DOL</h3>
    <p>Lorem ipsum dolor sit amet, consectetur adipi scing elit, sed do eiusmod tempor incididunt ut laborea.</p>
    <a class="btn-outline card-btn" href="#">Learn More</a>
  </article>
  <article class="service-card abs" style="left:780px">
    <div class="service-img" role="img" aria-label="Two women discussing work at a desk"></div>
    <h3>LOREM IPSUM DOL</h3>
    <p>Lorem ipsum dolor sit amet, consectetur adipi scing elit, sed do eiusmod tempor incididunt ut laborea.</p>
    <a class="btn-outline card-btn" href="#">Learn More</a>
  </article>
</section>

<section class="certs abs">
  <h2 class="section-title center certs-title abs"><span class="rule"></span><span>MY CERTIFICATIONS</span><span class="rule"></span></h2>
  <div class="badge-ring abs" style="left:265px"><div class="badge-core"><div class="badge-shape" role="img" aria-label="Certification badge"></div></div></div>
  <div class="badge-ring abs" style="left:504px"><div class="badge-core"><div class="badge-shape" role="img" aria-label="Certification badge"></div></div></div>
  <div class="badge-ring abs" style="left:742px"><div class="badge-core"><div class="badge-shape" role="img" aria-label="Certification badge"></div></div></div>
</section>

<section class="projects">
  <h2 class="section-title center projects-title abs"><span class="rule"></span><span><span class="light">PAST</span> PROJECTS</span><span class="rule"></span></h2>
  <div class="project abs" style="left:111px;top:2478px"><div class="project-img" style="height:264px" role="img" aria-label="Business handshake in a bright office"></div><h4>LOREM IPSUM</h4></div>
  <div class="project abs" style="left:360px;top:2527px"><div class="project-img" style="height:215px" role="img" aria-label="Team meeting in a lounge area"></div><h4 style="top:219px">LOREM IPSUM</h4></div>
  <div class="project abs" style="left:609px;top:2478px"><div class="project-img" style="height:264px" role="img" aria-label="Two colleagues reviewing a laptop"></div><h4>LOREM IPSUM</h4></div>
  <div class="project abs" style="left:857px;top:2527px"><div class="project-img" style="height:215px" role="img" aria-label="Professionals shaking hands"></div><h4 style="top:219px">LOREM IPSUM</h4></div>
</section>

<footer class="site-footer abs">
  <div class="footer-brand abs"><span class="brand-mark"></span><span class="brand-name">KEYSTONE<br>PROJECT CONSULTING</span></div>
  <div class="social footer-social abs" aria-label="Social profiles"><span class="primary">FB</span><span>TW</span><span>LI</span></div>

  <div class="footer-col abs" style="left:430px;top:54px">
    <h5>NAVIGATION</h5>
    <ul>
      <li><svg width="12" height="12"><circle cx="6" cy="6" r="6" fill="#666"/><path d="M5 3.5 7.5 6 5 8.5" stroke="#2f2f2f" stroke-width="1.5" fill="none"/></svg>Home</li>
      <li><svg width="12" height="12"><circle cx="6" cy="6" r="6" fill="#666"/><path d="M5 3.5 7.5 6 5 8.5" stroke="#2f2f2f" stroke-width="1.5" fill="none"/></svg>About Me</li>
      <li><svg width="12" height="12"><circle cx="6" cy="6" r="6" fill="#666"/><path d="M5 3.5 7.5 6 5 8.5" stroke="#2f2f2f" stroke-width="1.5" fill="none"/></svg>Services</li>
      <li><svg width="12" height="12"><circle cx="6" cy="6" r="6" fill="#666"/><path d="M5 3.5 7.5 6 5 8.5" stroke="#2f2f2f" stroke-width="1.5" fill="none"/></svg>Certifications</li>
      <li><svg width="12" height="12"><circle cx="6" cy="6" r="6" fill="#666"/><path d="M5 3.5 7.5 6 5 8.5" stroke="#2f2f2f" stroke-width="1.5" fill="none"/></svg>Projects</li>
    </ul>
  </div>

  <div class="footer-col abs" style="left:644px;top:54px">
    <h5>QUICK LINKS</h5>
    <ul>
      <li><svg width="12" height="12"><circle cx="6" cy="6" r="6" fill="#666"/><path d="M5 3.5 7.5 6 5 8.5" stroke="#2f2f2f" stroke-width="1.5" fill="none"/></svg>Privacy Policy</li>
      <li><svg width="12" height="12"><circle cx="6" cy="6" r="6" fill="#666"/><path d="M5 3.5 7.5 6 5 8.5" stroke="#2f2f2f" stroke-width="1.5" fill="none"/></svg>Terms Of Use</li>
      <li><svg width="12" height="12"><circle cx="6" cy="6" r="6" fill="#666"/><path d="M5 3.5 7.5 6 5 8.5" stroke="#2f2f2f" stroke-width="1.5" fill="none"/></svg>Blog</li>
      <li><svg width="12" height="12"><circle cx="6" cy="6" r="6" fill="#666"/><path d="M5 3.5 7.5 6 5 8.5" stroke="#2f2f2f" stroke-width="1.5" fill="none"/></svg>Contact Us</li>
    </ul>
  </div>

  <div class="footer-col abs" style="left:880px;top:54px;width:220px">
    <h5>CONTACT</h5>
    <ul>
      <li><svg width="12" height="14"><path d="M6 0a5 5 0 0 1 5 5c0 4-5 9-5 9S1 9 1 5a5 5 0 0 1 5-5z" fill="#666"/><circle cx="6" cy="5" r="1.8" fill="#2f2f2f"/></svg>465, Lorum Ipsum Dolore, United States</li>
      <li><svg width="13" height="13"><path d="M3 0 5.5 3 4 5a8 8 0 0 0 4 4l2-1.5 3 2.5-1.5 2.5C6 13 0 7 .5 1.5z" fill="#666"/></svg>+1 (555) 014 2290</li>
      <li><svg width="14" height="11"><rect width="14" height="11" rx="1" fill="#666"/><path d="M1 1.5 7 6l6-4.5" stroke="#2f2f2f" stroke-width="1.3" fill="none"/></svg>info@keystonepc.com</li>
    </ul>
  </div>

  <div class="footer-rule abs"></div>
  <p class="copyright abs">© 2022 <b>KEYSTONE</b> &nbsp;-&nbsp; All Rights Reserved</p>
</footer>

</body>
</html>
```